Flyer for the Lumen 2025 Conference

I am looking to produce a flyer for our upcoming conference, Lumen 2025. This is an annual conference that we plan to publicize on social media. The ideal designer will create a flyer that is eye-catching and effectively communicates the key information. Please see attached our logo, speaker photo, and flyer content.

Target Market(s)

All demographics

Industry/Entity Type

Christian

Font styles to use
Sans Serif

Requirements
Should not have
• Cross, church

```html
<!DOCTYPE html>
<html lang="en">
<head>
<meta charset="utf-8">
<title>Lumen 2025 Conference</title>
<link rel="stylesheet" href="https://fonts.googleapis.com/css2?family=Abril+Fatface&family=Montserrat:wght@200;300;400;600;700;800&family=Fira+Sans:wght@800&display=swap">
<style>
  :root {
    --navy-deep: #03081f;
    --navy: #0a1a5c;
    --royal: #1a4fd0;
    --cyan: #1fd6e8;
    --sky: #22a6f0;
    --orange: #f7962c;
    --ink: #0b1538;
    --white: #ffffff;
    --mist: #cfd8ea;
  }
  * { margin: 0; padding: 0; box-sizing: border-box; }
  html, body { width: 927px; height: 1200px; overflow: hidden; background: var(--navy-deep); }
  .flyer {
    position: relative;
    width: 927px;
    height: 1200px;
    overflow: hidden;
    font-family: "Montserrat", sans-serif;
    color: var(--white);
    background:
      radial-gradient(ellipse 380px 320px at 700px 330px, rgba(40,100,230,0.55), transparent 70%),
      radial-gradient(ellipse 300px 260px at 560px 820px, rgba(30,90,220,0.45), transparent 70%),
      radial-gradient(ellipse 520px 420px at 200px 760px, rgba(20,70,200,0.35), transparent 70%),
      linear-gradient(180deg, #0b2272 0%, #0a1b5a 40%, #061340 75%, var(--navy-deep) 100%);
  }
  .art { position: absolute; left: 0; top: 0; }
  .speaker-photo {
    position: absolute;
    left: 0; top: 379px;
    width: 527px; height: 752px;
    background: radial-gradient(ellipse 260px 380px at 220px 420px, #2a62d8 0%, #1a43a8 45%, rgba(10,30,90,0) 100%);
  }
  .month {
    position: absolute;
    left: 452px; top: 925px;
    transform: rotate(-90deg);
    transform-origin: 0 0;
    font-weight: 800;
    font-size: 62px;
    line-height: 52px;
    letter-spacing: -1px;
    background: linear-gradient(90deg, #2f8bf0, #1a55d8);
    -webkit-background-clip: text;
    background-clip: text;
    color: transparent;
  }
  .topic-label { position: absolute; left: 529px; top: 618px; font-size: 24px; font-weight: 400; color: var(--orange); }
  .topic-title {
    position: absolute; left: 525px; top: 655px; width: 334px; height: 41px;
    border-radius: 9px; background: var(--orange);
    font-family: "Fira Sans", sans-serif; font-weight: 800; font-size: 27px;
    color: var(--ink); text-align: center; line-height: 41px;
  }
  .schedule { position: absolute; left: 525px; top: 716px; width: 330px; }
  .session {
    position: relative; height: 54px; margin-bottom: 8px;
    background: linear-gradient(90deg, rgba(10,30,90,0) 0%, rgba(40,110,230,0.55) 50%, rgba(25,80,200,0.35) 85%, rgba(10,30,90,0) 100%);
  }
  .session-date { position: absolute; left: 5px; top: 2px; font-weight: 800; font-size: 46px; line-height: 50px; color: var(--orange); letter-spacing: -2px; }
  .session-date sup { font-size: 26px; vertical-align: 18px; letter-spacing: 0; margin-left: 2px; }
  .session-day { position: absolute; left: 125px; top: 8px; font-size: 18px; font-weight: 400; line-height: 20px; }
  .session-time { position: absolute; left: 125px; top: 29px; font-size: 18px; font-weight: 800; line-height: 20px; }
  .rule { position: absolute; height: 1px; background: var(--sky); }
  .venue-name { position: absolute; left: 525px; top: 930px; font-size: 17px; font-weight: 700; color: var(--orange); letter-spacing: 0.4px; }
  .pin-badge {
    position: absolute; left: 525px; top: 962px; width: 42px; height: 39px; border-radius: 10px;
    background: linear-gradient(135deg, var(--cyan), #1c8ff0);
    display: flex; align-items: center; justify-content: center;
  }
  .venue-address { position: absolute; left: 578px; top: 963px; font-size: 17px; line-height: 19px; letter-spacing: 1.2px; font-weight: 400; }
  .app-note { position: absolute; left: 526px; top: 1051px; font-size: 17px; line-height: 18.5px; font-weight: 400; }
  .app-note .app-name { color: var(--sky); }
  .org-mark { position: absolute; left: 714px; top: 1052px; display: flex; align-items: center; gap: 8px; }
  .org-mark .dot { width: 14px; height: 14px; border-radius: 50%; background: var(--orange); }
  .org-mark .org-name { font-weight: 400; font-size: 36px; letter-spacing: 1px; color: var(--white); }
  .speaker-label { position: absolute; left: 68px; top: 1016px; font-size: 28px; font-weight: 300; color: var(--orange); }
  .speaker-name { position: absolute; left: 68px; top: 1050px; font-size: 32px; font-weight: 800; line-height: 33px; }
  .contact-bar {
    position: absolute; left: 0; top: 1134px; width: 927px; height: 31px;
    background: linear-gradient(90deg, #1d9cf2, #1fb8ee 50%, #24e0ea);
    color: var(--ink); font-size: 20px; font-weight: 400; letter-spacing: 1px;
  }
  .contact-item { position: absolute; top: 2px; display: flex; align-items: center; gap: 7px; line-height: 27px; }
  .footer-base { position: absolute; left: 0; top: 1165px; width: 927px; height: 35px; background: #000; }
</style>
</head>
<body>
<main class="flyer">
  <div class="speaker-photo" role="img" aria-label="Photo of the speaker seated, wearing a blue suit, glasses and a grey knit sweater"></div>

  <svg class="art" width="927" height="560" viewBox="0 0 927 560" aria-hidden="false">
    <defs>
      <linearGradient id="gold" x1="0" y1="0" x2="0" y2="1">
        <stop offset="0" stop-color="#f8a33a"/>
        <stop offset="1" stop-color="#ee8a22"/>
      </linearGradient>
      <linearGradient id="aqua" x1="0" y1="0" x2="1" y2="0">
        <stop offset="0" stop-color="#1aa3c8"/>
        <stop offset="0.4" stop-color="#1fd6e8"/>
        <stop offset="1" stop-color="#22e0ee"/>
      </linearGradient>
    </defs>
    <text class="event-title" x="144" y="254" textLength="641" lengthAdjust="spacingAndGlyphs"
          font-family="'Abril Fatface', serif" font-size="212" fill="url(#gold)">LUMEN</text>
    <text class="event-year" x="158" y="338" font-family="'Abril Fatface', serif" font-size="74" letter-spacing="30" fill="url(#gold)">2025</text>
    <path d="M428 306 H735 Q785 306 785 360 V384" fill="none" stroke="#c9d6f2" stroke-opacity="0.7" stroke-width="1"/>
    <text x="297" y="450" textLength="490" lengthAdjust="spacingAndGlyphs" font-family="'Montserrat', sans-serif" font-weight="800" font-size="74" fill="url(#aqua)">A PROPHETIC</text>
    <text x="304" y="527" textLength="477" lengthAdjust="spacingAndGlyphs" font-family="'Montserrat', sans-serif" font-weight="200" font-size="72" fill="#dfe6f3">CONFERENCE</text>
  </svg>

  <div class="month">December</div>

  <div class="topic-label">Topic:</div>
  <div class="topic-title">The Voice Of The Lord</div>

  <section class="schedule">
    <div class="session"><div class="session-date">26<sup>th</sup></div><div class="session-day">Friday</div><div class="session-time">6:30PM - 9:00PM</div></div>
    <div class="session"><div class="session-date">27<sup>th</sup></div><div class="session-day">Saturday</div><div class="session-time">5:30PM - 8:00PM</div></div>
    <div class="session"><div class="session-date">28<sup>th</sup></div><div class="session-day">Sunday</div><div class="session-time">4:30PM - 7:00PM</div></div>
  </section>

  <div class="rule" style="left:525px; top:915px; width:334px;"></div>
  <div class="venue-name">The Harborview Performing Arts Center</div>
  <div class="pin-badge">
    <svg width="22" height="26" viewBox="0 0 22 26"><path d="M11 1C5.5 1 2 5 2 9.5 2 16 11 25 11 25s9-9 9-15.5C20 5 16.5 1 11 1z" fill="none" stroke="#0b1538" stroke-width="3"/><circle cx="11" cy="9.5" r="3" fill="#0b1538"/></svg>
  </div>
  <div class="venue-address">318 Linden Crest Avenue<br>Millbrook Falls, Maine 04000</div>

  <div class="rule" style="left:525px; top:1032px; width:183px;"></div>
  <div class="rule" style="left:741px; top:1032px; width:118px;"></div>
  <p class="app-note">Download the<br><span class="app-name">NEVAH App</span> to stay<br>updated on the event</p>
  <div class="org-mark"><span class="dot"></span><span class="org-name">NEVAH</span></div>

  <div class="speaker-label">SPEAKER:</div>
  <div class="speaker-name">PROPHET<br>ELIAS NATOMBO</div>

  <footer class="contact-bar">
    <div class="contact-item" style="left:69px;">
      <svg width="20" height="20" viewBox="0 0 20 20"><g fill="none" stroke="#0b1538" stroke-width="2"><circle cx="10" cy="10" r="8.5"/><ellipse cx="10" cy="10" rx="3.8" ry="8.5"/><path d="M1.5 10h17M3 5.5h14M3 14.5h14"/></g></svg>
      <span>www.nevah.org</span>
    </div>
    <div class="contact-item" style="left:359px;">
      <svg width="16" height="18" viewBox="0 0 16 18"><path d="M3 1l3 4-2 2c1 3 3 5 5 6l2-2 4 3-2 3C6 17 0 10 1 3z" fill="#0b1538"/></svg>
      <span>207 555 0142</span>
    </div>
    <div class="contact-item" style="left:620px;">
      <svg width="20" height="16" viewBox="0 0 20 16"><rect x="1" y="1" width="18" height="14" rx="2" fill="#0b1538"/><path d="M2.5 3l7.5 6 7.5-6" fill="none" stroke="#24d0ea" stroke-width="1.8"/></svg>
      <span>hello@nevah.org</span>
    </div>
  </footer>
  <div class="footer-base"></div>
</main>
</body>
</html>
```